Design concept Visual UI of future mobile app - healthcare

Hi,
I'm looking for a top designer, innovative with strong experience in user interface

The app will be connected to a future health website related to depression and addiction by helping the user to track the moods, tired, anxiety using this mobile app.

I attached the deck of the overall project but I can send you a specific presentation for the app only

thanks

Target Market(s)

Switzerland, UK, Germany and France

Industry/Entity Type

Mental Health

Logo Text

Health, hope

Font styles to use
Sans Serif

Colors
cee9f5
33a6d7
0692cd
0255a3
3276b5
85abd2

Requirements
Must have
• keep it simple, easy to navigate
• The user should be able to track the moods on a daily basis,
• sleep time, and rate how the feel on the day
• To be able to get information from the sync deck of vexlo
Nice to have
• to be able share this app with a friend

```html
<!DOCTYPE html>
<html lang="en">
<head>
<meta charset="utf-8">
<title>Health, hope – App screens</title>
<link href="https://fonts.googleapis.com/css2?family=Roboto:wght@400;500;700&display=swap" rel="stylesheet">
<style>
:root{
  --bg:#f2f2f2;
  --sky-top:#3a93d6;
  --sky-mid:#5fa9df;
  --sky-low:#84bbe3;
  --header:#2f86cf;
  --sidebar:rgba(96,128,150,.55);
  --highlight:#6b6f72;
  --band:rgba(190,220,240,.45);
  --ink:#ffffff;
  --ink-soft:#eaf4fb;
  --bubble:#ffffff;
  --bubble-ink:#333333;
  --stamp:#3276b5;
  --status-dark:#111111;
}
*{margin:0;padding:0;box-sizing:border-box}
html,body{width:1200px;height:800px;overflow:hidden;background:var(--bg);font-family:'Roboto',Arial,sans-serif}
.stage{position:relative;width:1200px;height:800px}
.screen{position:absolute;top:227px;width:189px;height:335px;overflow:hidden;
  background:linear-gradient(180deg,var(--sky-top) 0%,var(--sky-mid) 45%,var(--sky-low) 100%)}
.screen--one{left:233px}.screen--two{left:510px}.screen--three{left:786px}

.status{position:absolute;left:0;top:0;width:100%;height:13px;background:var(--status-dark);color:#fff;
  font-size:5.5px;display:flex;align-items:center;justify-content:space-between;padding:0 4px}
.status--light{background:#fff;color:#111}
.status .time{position:absolute;left:50%;transform:translateX(-50%);font-weight:500}
.battery{display:inline-block;width:12px;height:5px;border:1px solid currentColor;border-radius:1px;margin-left:2px;vertical-align:middle;background:currentColor}

.header{position:absolute;left:0;top:13px;width:100%;height:28px;background:var(--header);color:var(--ink);
  display:flex;align-items:center;font-size:8px;font-weight:700;letter-spacing:.2px}
.header .burger{position:absolute;left:19px;top:10px}
.header .prev{position:absolute;left:38px;top:8px}
.header .next{position:absolute;right:22px;top:8px}
.header .title{position:absolute;left:48px;right:30px;text-align:center;display:flex;align-items:center;justify-content:center;gap:3px}

.sidebar{position:absolute;left:0;top:41px;width:108px;bottom:0;background:var(--sidebar)}
.menu-item{position:absolute;left:0;width:108px;height:25px;display:flex;align-items:center;gap:5px;padding-left:5px;
  color:var(--ink);font-size:7.2px;font-weight:700}
.menu-item--active{background:var(--highlight)}
.sub-item{position:absolute;left:23px;color:var(--ink-soft);font-size:5.2px;font-weight:500;text-transform:uppercase}
.logout{position:absolute;left:90px;top:230px}

.content{position:absolute;left:108px;top:41px;right:0;bottom:0;color:var(--ink);font-size:7.5px}
.owner{position:absolute;left:68px;top:5px;white-space:nowrap;font-size:7px}
.avatar{position:absolute;background:linear-gradient(160deg,#d9b48f,#8a6a4e)}
.avatar--profile{left:41px;top:23px;width:40px;height:49px;border:1px solid #fff}
.row{position:absolute;left:15px;display:flex;align-items:center;gap:3px;white-space:nowrap}
.row--plain{left:26px}
.band{position:absolute;left:0;right:0;height:17px;background:var(--band);padding-left:14px;display:flex;align-items:center;white-space:nowrap}

.chat-avatar{position:absolute;left:122px;width:43px;height:50px;border:1px solid #fff;background:linear-gradient(160deg,#f0d7a8,#9bb7cf)}
.bubble{position:absolute;background:var(--bubble);border-radius:3px;color:var(--bubble-ink);font-size:4.3px;padding:5px 4px;white-space:nowrap;box-shadow:0 1px 2px rgba(0,0,0,.15)}
.bubble .stamp{color:var(--stamp);display:block;margin-bottom:9px}
</style>
</head>
<body>
<div class="stage">

  <!-- Personal information screen -->
  <section class="screen screen--one">
    <div class="status"><span>●●●○○ NOVA</span><span class="time">4:21 PM</span><span>100%<i class="battery"></i></span></div>
    <header class="header">
      <svg class="burger" width="10" height="8" viewBox="0 0 10 8"><path d="M0 1h10M0 4h10M0 7h10" stroke="#fff" stroke-width="1.3"/></svg>
      <svg class="prev" width="6" height="11" viewBox="0 0 6 11"><path d="M5 1 1 5.5 5 10" fill="none" stroke="#fff" stroke-width="1"/></svg>
      <span class="title">PERSONAL INFORMATION</span>
      <svg class="next" width="6" height="11" viewBox="0 0 6 11"><path d="M1 1l4 4.5L1 10" fill="none" stroke="#fff" stroke-width="1"/></svg>
    </header>
    <nav class="sidebar">
      <div class="menu-item menu-item--active" style="top:0"><svg width="8" height="8" viewBox="0 0 8 8"><path d="M4 0 0 4h1v4h2V5h2v3h2V4h1z" fill="#fff"/></svg>HOME SCREEN</div>
      <span class="sub-item" style="top:37px">How I feel today</span>
      <span class="sub-item" style="top:57px">Tracking graphs</span>
      <span class="sub-item" style="top:79px">Personal information</span>
      <div class="menu-item menu-item--active" style="top:90px"><svg width="9" height="8" viewBox="0 0 9 8"><rect x=".5" y="1.5" width="6" height="6" fill="none" stroke="#fff"/><path d="M3 5l5-5" stroke="#fff"/></svg>ACTIVITY</div>
      <div class="menu-item" style="top:112px"><svg width="8" height="7" viewBox="0 0 8 7"><path d="M0 2l4 2.5L8 2v5H0zM4 0l4 2H0z" fill="#fff"/></svg>MESSAGES</div>
      <div class="menu-item" style="top:133px"><svg width="7" height="8" viewBox="0 0 7 8"><circle cx="3.5" cy="2" r="2" fill="#fff"/><path d="M0 8c0-3 7-3 7 0z" fill="#fff"/></svg>PROFILE</div>
      <div class="menu-item" style="top:155px"><svg width="8" height="8" viewBox="0 0 8 8"><circle cx="4" cy="4" r="2.8" fill="none" stroke="#fff" stroke-width="2" stroke-dasharray="1.4 .8"/><circle cx="4" cy="4" r="1" fill="#fff"/></svg>SETTING</div>
      <svg class="logout" width="12" height="10" viewBox="0 0 12 10"><path d="M0 5h6M4 3l2 2-2 2" stroke="#fff" fill="none"/><rect x="8" y="0" width="3" height="10" fill="#fff"/></svg>
    </nav>
    <div class="content">
      <span class="owner">Mark Evans</span>
      <div class="avatar avatar--profile" role="img" aria-label="Profile photo of the user"></div>
      <div class="row" style="top:80px">✎ Medications</div>
      <div class="row" style="top:93px">▤ Consultations</div>
      <div class="row" style="top:106px">♥ Health Check</div>
      <div class="band" style="top:125px">Friend and Family</div>
      <div class="row" style="top:149px">● Emily</div>
      <div class="row" style="top:162px">● Jackson</div>
      <div class="row" style="top:175px">⊕ Add Profile</div>
      <div class="band" style="top:195px">Most recently diagnosed</div>
      <div class="row row--plain" style="top:217px">Depression</div>
      <div class="row row--plain" style="top:230px">Anxiety</div>
    </div>
  </section>

  <!-- Messages screen -->
  <section class="screen screen--two">
    <div class="status status--light"><span>●●●○○ NOVA</span><span class="time">4:21 PM</span><span>100%<i class="battery"></i></span></div>
    <header class="header">
      <svg class="burger" width="10" height="8" viewBox="0 0 10 8"><path d="M0 1h10M0 4h10M0 7h10" stroke="#fff" stroke-width="1.3"/></svg>
      <svg class="prev" width="6" height="11" viewBox="0 0 6 11"><path d="M5 1 1 5.5 5 10" fill="none" stroke="#fff" stroke-width="1"/></svg>
      <span class="title"><svg width="8" height="7" viewBox="0 0 8 7"><path d="M0 2l4 2.5L8 2v5H0zM4 0l4 2H0z" fill="#fff"/></svg>MESSAGES</span>
      <svg class="next" width="6" height="11" viewBox="0 0 6 11"><path d="M1 1l4 4.5L1 10" fill="none" stroke="#fff" stroke-width="1"/></svg>
    </header>
    <nav class="sidebar">
      <div class="menu-item menu-item--active" style="top:0"><svg width="8" height="8" viewBox="0 0 8 8"><path d="M4 0 0 4h1v4h2V5h2v3h2V4h1z" fill="#fff"/></svg>HOME SCREEN</div>
      <span class="sub-item" style="top:37px">How I feel today</span>
      <span class="sub-item" style="top:57px">Tracking graphs</span>
      <span class="sub-item" style="top:79px">Personal information</span>
      <div class="menu-item menu-item--active" style="top:90px"><svg width="9" height="8" viewBox="0 0 9 8"><rect x=".5" y="1.5" width="6" height="6" fill="none" stroke="#fff"/><path d="M3 5l5-5" stroke="#fff"/></svg>ACTIVITY</div>
      <div class="menu-item" style="top:112px"><svg width="8" height="7" viewBox="0 0 8 7"><path d="M0 2l4 2.5L8 2v5H0zM4 0l4 2H0z" fill="#fff"/></svg>MESSAGES</div>
      <div class="menu-item" style="top:133px"><svg width="7" height="8" viewBox="0 0 7 8"><circle cx="3.5" cy="2" r="2" fill="#fff"/><path d="M0 8c0-3 7-3 7 0z" fill="#fff"/></svg>PROFILE</div>
      <div class="menu-item" style="top:155px"><svg width="8" height="8" viewBox="0 0 8 8"><circle cx="4" cy="4" r="2.8" fill="none" stroke="#fff" stroke-width="2" stroke-dasharray="1.4 .8"/><circle cx="4" cy="4" r="1" fill="#fff"/></svg>SETTING</div>
      <svg class="logout" width="12" height="10" viewBox="0 0 12 10"><path d="M0 5h6M4 3l2 2-2 2" stroke="#fff" fill="none"/><rect x="8" y="0" width="3" height="10" fill="#fff"/></svg>
    </nav>
    <div class="chat-avatar" role="img" aria-label="Photo of the counsellor" style="top:49px"></div>
    <div class="bubble" style="left:172px;top:50px;width:40px;height:40px"><span class="stamp">2 min ago</span>Hi! How did you sleep?</div>
    <div class="bubble" style="left:137px;top:111px;width:60px;height:38px"><span class="stamp">3 minutes ago</span>Thanks. Do you have any news?</div>
    <div class="chat-avatar" role="img" aria-label="Photo of the counsellor" style="top:172px"></div>
    <div class="bubble" style="left:172px;top:172px;width:40px;height:38px"><span class="stamp">1 min ago</span>I feel much better today.</div>
    <div class="bubble" style="left:134px;top:237px;width:60px;height:38px"><span class="stamp">1 minutes ago</span>Thanks.</div>
    <div class="bubble" style="left:134px;top:301px;width:60px;height:40px"><span class="stamp">1 minutes ago</span>Thanks.</div>
  </section>

  <!-- Personal information screen, second variant -->
  <section class="screen screen--three">
    <div class="status"><span>●●●○○ NOVA</span><span class="time">4:21 PM</span><span>100%<i class="battery"></i></span></div>
    <header class="header">
      <svg class="burger" width="10" height="8" viewBox="0 0 10 8"><path d="M0 1h10M0 4h10M0 7h10" stroke="#fff" stroke-width="1.3"/></svg>
      <svg class="prev" width="6" height="11" viewBox="0 0 6 11"><path d="M5 1 1 5.5 5 10" fill="none" stroke="#fff" stroke-width="1"/></svg>
      <span class="title">PERSONAL INFORMATION</span>
      <svg class="next" width="6" height="11" viewBox="0 0 6 11"><path d="M1 1l4 4.5L1 10" fill="none" stroke="#fff" stroke-width="1"/></svg>
    </header>
    <nav class="sidebar">
      <div class="menu-item menu-item--active" style="top:0"><svg width="8" height="8" viewBox="0 0 8 8"><path d="M4 0 0 4h1v4h2V5h2v3h2V4h1z" fill="#fff"/></svg>HOME SCREEN</div>
      <span class="sub-item" style="top:37px">How I feel today</span>
      <span class="sub-item" style="top:57px">Tracking graphs</span>
      <span class="sub-item" style="top:79px">Personal information</span>
      <div class="menu-item menu-item--active" style="top:90px"><svg width="9" height="8" viewBox="0 0 9 8"><rect x=".5" y="1.5" width="6" height="6" fill="none" stroke="#fff"/><path d="M3 5l5-5" stroke="#fff"/></svg>ACTIVITY</div>
      <div class="menu-item" style="top:112px"><svg width="8" height="7" viewBox="0 0 8 7"><path d="M0 2l4 2.5L8 2v5H0zM4 0l4 2H0z" fill="#fff"/></svg>MESSAGES</div>
      <div class="menu-item" style="top:133px"><svg width="7" height="8" viewBox="0 0 7 8"><circle cx="3.5" cy="2" r="2" fill="#fff"/><path d="M0 8c0-3 7-3 7 0z" fill="#fff"/></svg>PROFILE</div>
      <div class="menu-item" style="top:155px"><svg width="8" height="8" viewBox="0 0 8 8"><circle cx="4" cy="4" r="2.8" fill="none" stroke="#fff" stroke-width="2" stroke-dasharray="1.4 .8"/><circle cx="4" cy="4" r="1" fill="#fff"/></svg>SETTING</div>
      <svg class="logout" width="12" height="10" viewBox="0 0 12 10"><path d="M0 5h6M4 3l2 2-2 2" stroke="#fff" fill="none"/><rect x="8" y="0" width="3" height="10" fill="#fff"/></svg>
    </nav>
    <div class="content">
      <span class="owner">Mark Evans</span>
      <div class="avatar avatar--profile" role="img" aria-label="Profile photo of the user"></div>
      <div class="row" style="top:80px">✎ Medications</div>
      <div class="row" style="top:93px">▤ Consultations</div>
      <div class="row" style="top:106px">♥ Health Check</div>
      <div class="band" style="top:125px">Friend and Family</div>
      <div class="row" style="top:149px">● Emily</div>
      <div class="row" style="top:162px">● Jackson</div>
      <div class="row" style="top:175px">⊕ Add Profile</div>
      <div class="band" style="top:195px">Most recently diagnosed</div>
      <div class="row row--plain" style="top:217px">Depression</div>
      <div class="row row--plain" style="top:230px">Anxiety</div>
    </div>
  </section>

</div>
</body>
</html>
```